New Bicycle shop business card

Hi!
I'm looking for a business card for my new proffesional bike mechanics shop. This shop is only for fixing broken bikes and not selling bikes.
Peferbly a modern and sleek and modern design.
Colors: black, grey, red, white
Information:
Name: Rijwielwerkplaats Vanhoutte
Shop owner: Bart Vanhoutte & Marieke Segers
Website: www.rijwielwerkplaats-vanhoutte.be
Email: info@rijwielwerkplaats-vanhoutte.be
Phone number: +32471902368
Street adres: Kerkweg 46
9940 Bellebeke
Slogan/shop information: Herstellingen van alle merken.
Logo: see files.
Target Market(s)
People who seek a mechanic to fix or upgrade their bikes.
Contact Information for Business Card
Information:
Website: info@rijwielwerkplaats-vanhoutte.be
9940 Bellebeke
Logo: see files.

```html
<!DOCTYPE html>
<html lang="nl">
<head>
<meta charset="utf-8">
<title>Rijwielwerkplaats Vanhoutte – visitekaartje</title>
<link href="https://fonts.googleapis.com/css2?family=Open+Sans:wght@400;600;700;800&display=swap" rel="stylesheet">
<style>
  :root {
    --stage: #3a3b3d;
    --card-black: #0a0a0a;
    --card-white: #ffffff;
    --brand-red: #e3223f;
    --text-grey: #8a8a8a;
    --text-dark: #111111;
    --pattern-tone: #161616;
  }
  * { box-sizing: border-box; margin: 0; padding: 0; }
  html, body {
    width: 1200px; height: 900px; overflow: hidden;
    background: var(--stage);
    font-family: "Open Sans", Arial, sans-serif;
  }
  .stage {
    width: 1200px; height: 900px;
    display: flex; flex-direction: column; align-items: center; justify-content: center;
    gap: 54px;
  }
  .card {
    width: 600px; height: 343px;
    border-radius: 26px;
    position: relative; overflow: hidden;
    box-shadow: 0 14px 34px rgba(0,0,0,.45);
  }

  /* Front */
  .card--front { background: var(--card-black); }
  .card__pattern {
    position: absolute; inset: 0;
    background: radial-gradient(ellipse at 60% 40%, var(--pattern-tone), var(--card-black) 75%);
  }
  .front__content {
    position: absolute; inset: 0;
    display: flex; flex-direction: column; align-items: center; justify-content: center;
  }
  .brand { display: flex; align-items: center; gap: 12px; }
  .brand__dot {
    width: 22px; height: 22px; border-radius: 50%;
    background: var(--brand-red); flex: none;
  }
  .brand__name {
    font-weight: 800; font-size: 25px; letter-spacing: 2px;
    text-transform: uppercase; color: #ffffff;
  }
  .front__slogan {
    margin-top: 46px;
    color: #ffffff; font-size: 13px; font-weight: 600;
  }

  /* Back */
  .card--back { background: var(--card-white); display: flex; align-items: center; }
  .back__brand {
    flex: none; width: 270px; padding: 0 16px 30px 36px;
    display: flex; flex-direction: column; align-items: flex-start; gap: 12px;
  }
  .back__brand .brand__square {
    width: 28px; height: 28px; background: var(--brand-red);
  }
  .back__brand .brand__name {
    color: var(--brand-red); font-size: 18px; letter-spacing: .5px; line-height: 1.25;
  }
  .divider {
    flex: none; width: 1px; height: 160px; background: var(--brand-red);
    margin: 0 22px 30px 0;
  }
  .details { flex: 1; min-width: 0; margin-bottom: 30px; padding-right: 20px; }
  .details__label { color: var(--brand-red); font-size: 13px; font-weight: 600; }
  .details__owners { color: var(--text-grey); font-size: 15px; font-weight: 700; white-space: nowrap; }
  .details__company { margin-top: 8px; color: var(--brand-red); font-size: 16px; font-weight: 700; }
  .details__role { color: var(--text-dark); font-size: 12px; font-weight: 600; }
  .contact { list-style: none; margin-top: 10px; }
  .contact__item {
    display: flex; align-items: center; gap: 8px;
    color: var(--text-grey); font-size: 12px; line-height: 1.6; white-space: nowrap;
  }
  .contact__icon { width: 11px; height: 11px; flex: none; }
  .back__address {
    position: absolute; left: 270px; right: 30px; bottom: 26px;
    color: var(--text-grey); font-size: 14px; text-align: center;
  }
</style>
</head>
<body>
<main class="stage">

  <section class="card card--front">
    <div class="card__pattern" role="img" aria-label="Faint repeating emblem pattern on black"></div>
    <div class="front__content">
      <div class="brand">
        <span class="brand__dot"></span>
        <span class="brand__name">Rijwielwerkplaats Vanhoutte</span>
      </div>
      <p class="front__slogan">Herstellingen van alle merken.</p>
    </div>
  </section>

  <section class="card card--back">
    <div class="back__brand">
      <span class="brand__square"></span>
      <span class="brand__name">Rijwielwerkplaats<br>Vanhoutte</span>
    </div>
    <div class="divider"></div>
    <div class="details">
      <p class="details__label">Shop owner:</p>
      <p class="details__owners">Bart Vanhoutte &amp; Marieke Segers</p>
      <p class="details__company">Rijwielwerkplaats Vanhoutte</p>
      <p class="details__role">General Manager</p>
      <ul class="contact">
        <li class="contact__item">
          <svg class="contact__icon" viewBox="0 0 24 24"><path fill="#e3223f" d="M6.6 10.8a15 15 0 0 0 6.6 6.6l2.2-2.2c.3-.3.7-.4 1-.2 1.1.4 2.3.6 3.6.6.6 0 1 .4 1 1V20c0 .6-.4 1-1 1A17 17 0 0 1 3 4c0-.6.4-1 1-1h3.5c.6 0 1 .4 1 1 0 1.3.2 2.5.6 3.6.1.3 0 .7-.2 1z"/></svg>
          +32471902368
        </li>
        <li class="contact__item">
          <svg class="contact__icon" viewBox="0 0 24 24"><path fill="#e3223f" d="M2 5h20v14H2zm2 2v.5l8 5 8-5V7z"/></svg>
          info@rijwielwerkplaats-vanhoutte.be
        </li>
        <li class="contact__item">
          <svg class="contact__icon" viewBox="0 0 24 24"><circle cx="12" cy="12" r="10" fill="#e3223f"/><path d="M2 12h20M12 2c3 3 3 17 0 20M12 2c-3 3-3 17 0 20" stroke="#fff" stroke-width="1.5" fill="none"/></svg>
          www.rijwielwerkplaats-vanhoutte.be
        </li>
      </ul>
    </div>
    <p class="back__address">Kerkweg 46 9940 Bellebeke</p>
  </section>

</main>
</body>
</html>
```